Construction Company Cellar Crafters needs Business Card

I would like modern looking business card design. I am attaching logo of our company. Please include cell nr 302.418.7650 , email address cellarcrafters4u@examplemail.com, web : cellarcrafters4u.com, please also include wording: Specializing in finishing and remodeling basements. You can play with dark grey and orange colors or any ideas are welcome. Also include social media icons Friendloop and HouseGuidr.

```html
<!DOCTYPE html>
<html lang="en">
<head>
<meta charset="utf-8">
<title>Cellar Crafters – Business Card</title>
<link href="https://fonts.googleapis.com/css2?family=Michroma&family=Open+Sans:wght@400;600&display=swap" rel="stylesheet">
<style>
  :root {
    --orange: #ec5a2a;
    --white: #ffffff;
    --paper: #f7f7f6;
    --ink: #2b2b2b;
    --grey: #555555;
    --backdrop: #e9e9ea;
  }
  * { box-sizing: border-box; margin: 0; padding: 0; }
  html, body {
    width: 1200px; height: 900px; overflow: hidden;
    background: var(--backdrop);
    font-family: "Open Sans", Arial, sans-serif;
  }
  .sheet {
    width: 1200px; height: 900px;
    display: flex; align-items: center; justify-content: center; gap: 40px;
  }
  .card {
    position: relative;
    width: 540px; height: 309px;
    overflow: hidden;
    box-shadow: 0 8px 24px rgba(0,0,0,0.12);
  }

  /* Front */
  .card-front { background: var(--paper); }
  .holder { position: absolute; left: 36px; top: 34px; }
  .holder-name {
    font-family: "Michroma", sans-serif;
    color: var(--orange); font-size: 17px; letter-spacing: 1px;
  }
  .holder-title { color: var(--ink); font-size: 11px; margin-top: 3px; }
  .contact-list {
    position: absolute; left: 36px; top: 100px;
    list-style: none; font-size: 12px; color: var(--grey); line-height: 19px;
  }
  .contact-list li { display: flex; align-items: center; gap: 7px; }
  .contact-list svg { width: 10px; height: 10px; flex: none; }
  .brand {
    font-family: "Michroma", sans-serif;
    display: flex; align-items: center; gap: 10px;
    white-space: nowrap;
  }
  .brand-mark { width: 14px; height: 14px; flex: none; }
  .brand-name { font-size: 24px; letter-spacing: 1px; line-height: 1; }
  .card-front .brand { position: absolute; right: 34px; top: 186px; }
  .card-front .brand-name { color: var(--orange); font-size: 22px; }
  .card-front .brand-mark { background: var(--ink); }
  .tagline-band {
    position: absolute; left: 0; right: 0; bottom: 18px; height: 42px;
    background: var(--orange); color: var(--white);
    display: flex; align-items: center; padding-left: 36px;
    font-size: 13px; text-transform: uppercase; letter-spacing: 0.3px;
  }

  /* Back */
  .card-back { background: var(--orange); }
  .card-back .brand { position: absolute; left: 0; right: 0; top: 88px; justify-content: center; }
  .card-back .brand-name { color: var(--white); font-size: 30px; }
  .card-back .brand-mark { background: var(--white); width: 16px; height: 16px; }
  .social-band {
    position: absolute; left: 0; right: 0; bottom: 14px; height: 68px;
    background: var(--white);
    display: flex; align-items: center; justify-content: center; gap: 34px;
    font-size: 13px; font-weight: 600; color: var(--ink);
  }
  .social-item { display: flex; align-items: center; gap: 8px; }
  .social-dot { width: 18px; height: 18px; border-radius: 50%; background: var(--orange); }
</style>
</head>
<body>
<main class="sheet">
  <section class="card card-front" aria-label="Business card front">
    <div class="holder">
      <p class="holder-name">DANIEL BROOKS</p>
      <p class="holder-title">Managing Director</p>
    </div>
    <ul class="contact-list">
      <li><svg viewBox="0 0 10 10"><rect x="2" y="0.5" width="6" height="9" rx="1" fill="none" stroke="var(--orange)" stroke-width="1.3"/></svg>302.418.7650</li>
      <li><svg viewBox="0 0 10 10"><rect x="0.5" y="2" width="9" height="6" fill="var(--orange)"/><path d="M0.5 2 L5 5.5 L9.5 2" fill="none" stroke="#fff" stroke-width="0.9"/></svg>cellarcrafters4u@examplemail.com</li>
      <li><svg viewBox="0 0 10 10"><circle cx="5" cy="5" r="4.3" fill="var(--orange)"/><path d="M0.7 5 H9.3 M5 0.7 C2.5 3 2.5 7 5 9.3 M5 0.7 C7.5 3 7.5 7 5 9.3" fill="none" stroke="#fff" stroke-width="0.7"/></svg>cellarcrafters4u.com</li>
    </ul>
    <div class="brand">
      <span class="brand-mark"></span>
      <span class="brand-name">CELLAR CRAFTERS</span>
    </div>
    <div class="tagline-band">Specializing in finishing and remodeling basements.</div>
  </section>

  <section class="card card-back" aria-label="Business card back">
    <div class="brand">
      <span class="brand-mark"></span>
      <span class="brand-name">CELLAR CRAFTERS</span>
    </div>
    <div class="social-band">
      <span class="social-item"><span class="social-dot"></span>Friendloop</span>
      <span class="social-item"><span class="social-dot"></span>HouseGuidr</span>
    </div>
  </section>
</main>
</body>
</html>
```